Corvena Hotel, city center modern minimal hotel operating all year round, on Rhodes island Greece

city, modern ,all year operating hotel

Target Market(s)

tourists, business agents

Industry/Entity Type

tourism

Number of Pages Required

2 page

Requirements
Must have
• room type photos and descriptions, amenities individual listing (graphic), comments sections, map driving location details
Nice to have
• gallery section, modern and minimal design, amenities section, individual room type descriptions, photos and facilities

```html
<!DOCTYPE html>
<html lang="en">
<head>
<meta charset="utf-8">
<title>Corvena Hotel – Home</title>
<link rel="stylesheet" href="https://fonts.googleapis.com/css2?family=Barlow:wght@400;500;600&family=Gelasio:wght@400&display=swap">
<style>
:root{
  --gold:#b28a56;
  --dark:#232323;
  --ink:#3a3a3a;
  --muted:#8c8c8c;
  --cream:#f2ede4;
  --footer:#f4f1eb;
  --line:#e6e2da;
  --stage:#000;
}
html,body{margin:0;padding:0}
body{width:1200px;height:1200px;overflow:hidden;background:var(--stage);position:relative}
.panel{position:absolute;overflow:hidden;background:#fff}
.panel-full{left:11px;top:9px;width:270px;height:1174px}
.panel-top{left:407px;top:11px;width:385px;height:1172px}
.panel-bottom{left:803px;top:12px;width:384px;height:514px}
.page{position:absolute;left:0;top:0;width:619px;height:2695px;transform-origin:0 0;font-family:'Barlow',sans-serif;color:var(--ink);background:#fff}
.panel-full .page{transform:scale(.4362)}
.panel-top .page{transform:scale(.622)}
.panel-bottom .page{transform:scale(.6204) translateY(-1867px)}
.page p,.page h1,.page h2,.page h3,.page h4{margin:0;font-weight:400}
.band{position:absolute;left:0;width:619px}
.abs{position:absolute}

/* nav */
.nav{top:0;height:30px;background:#fff}
.brand{position:absolute;left:90px;top:9px;display:flex;align-items:center;gap:5px}
.brand-mark{width:10px;height:10px;background:var(--gold)}
.brand-name{font-family:'Gelasio',serif;font-weight:400;font-size:11px;color:var(--gold);letter-spacing:.4px;line-height:12px}
.menu{position:absolute;left:258px;top:12px;display:flex;gap:12px;align-items:center;font-size:4.6px;letter-spacing:.4px;text-transform:uppercase;color:#444;line-height:6px}
.menu .on{color:var(--gold)}
.menu-div{width:.6px;height:9px;background:var(--gold)}
.flag{width:9px;height:6px;border:.6px solid #444;border-radius:1px;box-sizing:border-box}

/* hero */
.hero-photo{top:30px;height:304px;background:radial-gradient(ellipse at 30% 30%,rgba(140,115,80,.45),transparent 55%),radial-gradient(ellipse at 80% 55%,rgba(110,90,60,.35),transparent 50%),linear-gradient(180deg,#2b2824,#3e352a 45%,#1d1a17)}
.hero-title{top:117px;left:0;width:619px;text-align:center;color:#fff;font-family:'Gelasio',serif;font-size:22px;line-height:24px}
.hero-sub{top:152px;left:0;width:619px;text-align:center;color:#fff;font-size:4.8px;letter-spacing:1.2px;font-weight:600}
.hero-btn{top:185px;left:276px;width:66px;height:18px;box-sizing:border-box;border:.8px solid #fff;color:#fff;font-size:4.8px;letter-spacing:1px;font-weight:600;display:flex;align-items:center;justify-content:center}
.booking{top:292px;left:95px;width:429px;height:22px;background:#fff;display:flex;font-size:5px;color:#555}
.field{height:22px;box-sizing:border-box;border-right:.6px solid #ddd;display:flex;align-items:center;justify-content:space-between;padding:0 7px}
.field svg{width:5px;height:5px}
.f1{width:73px}.f2{width:70px}.f3{width:52px}.f4{width:57px}.f5{width:52px}.f6{width:57px;border:0}
.check{width:68px;background:var(--gold);color:#fff;font-weight:600;letter-spacing:.8px;justify-content:center;border:0}

/* intro */
.intro{top:354px;left:112px;width:395px;text-align:center;font-family:'Gelasio',serif;font-weight:400;font-size:10.4px;line-height:19.4px;color:#333}

/* section heads */
.eyebrow{position:absolute;left:95px;font-size:4.5px;letter-spacing:2px;color:#8a8a8a;text-transform:uppercase;line-height:6px}
.h2{position:absolute;left:95px;font-family:'Gelasio',serif;font-weight:400;font-size:16px;line-height:18px;color:#222}
.center{left:0;width:619px;text-align:center}

/* room cards */
.rooms{top:493px;height:278px;background:var(--cream)}
.rooms .eyebrow{top:22px}.rooms .h2{top:34px}
.card{position:absolute;overflow:hidden}
.card-photo{position:absolute;inset:0}
.card-fade{position:absolute;left:0;right:0;bottom:0;height:60%;background:linear-gradient(180deg,transparent,rgba(20,16,12,.7))}
.book{position:absolute;right:6px;top:6px;width:11px;height:24px;box-sizing:border-box;border:.6px solid #fff;background:rgba(30,25,20,.55);color:#fff;font-size:4.4px;font-weight:600;letter-spacing:.5px;display:flex;align-items:center;justify-content:center}
.book span{transform:rotate(-90deg);display:block}
.card-info{position:absolute;left:12px;right:12px;bottom:14px;color:#fff}
.price{font-size:4.8px;font-weight:600;letter-spacing:.8px;text-transform:uppercase}
.card-name{font-family:'Gelasio',serif;font-weight:400;font-size:12px;line-height:15px;margin-top:3px}
.rule{display:block;width:18px;height:.8px;background:var(--gold);margin-top:4px}
.desc{font-size:5px;line-height:6.4px;margin-top:4px;color:#eee}
.amenity-row{display:flex;justify-content:space-between;align-items:center;margin-top:7px}
.amenities{display:flex;gap:4px}
.amenities i{width:7px;height:6px;border:.6px solid #fff;border-radius:1px;box-sizing:border-box}
.details{font-size:4.8px;font-weight:600;letter-spacing:.8px}
.r1{left:95px;top:69px;width:135px;height:181px}
.r2{left:242px;top:69px;width:135px;height:181px}
.r3{left:388px;top:69px;width:136px;height:181px}
.p-classic{background:linear-gradient(160deg,#9a8b78,#5a4c3e 55%,#2e261f)}
.p-exec{background:linear-gradient(170deg,#7d7061,#4a3f34 60%,#2b231d)}
.p-sup{background:linear-gradient(150deg,#8f806d,#5d4f41 55%,#3a3028)}
.p-family{background:linear-gradient(160deg,#857766,#55483b 55%,#2d261f)}
.p-rector{background:linear-gradient(155deg,#938473,#625344 55%,#362c24)}

/* suite */
.suite{top:771px;height:279px;background:var(--dark)}
.suite .eyebrow{top:42px;color:#9a9a9a}
.suite .h2{top:54px;color:#fff}
.suite-phone{position:absolute;left:95px;top:90px;display:flex;gap:6px;align-items:center}
.suite-phone svg{width:11px;height:11px}
.suite-phone .lbl{font-size:4.4px;letter-spacing:.8px;color:#ddd;font-weight:600}
.suite-phone .num{font-size:6.5px;color:var(--gold);margin-top:2px}
.s1{left:195px;top:42px;width:159px;height:181px}
.s2{left:365px;top:42px;width:159px;height:181px}
.dots{position:absolute;display:flex;gap:2.5px;align-items:center}
.dots i{width:4px;height:4px;border-radius:50%;border:.6px solid #999;box-sizing:border-box}
.dots i.on{background:var(--gold);border-color:var(--gold)}
.dots i.wide{width:10px;border-radius:3px}
.suite .dots{left:302px;top:241px}

/* facilities */
.facilities{top:1050px;height:301px;background:#fff}
.facilities .eyebrow{top:30px}.facilities .h2{top:41px}
.fac{position:absolute;width:135px;height:93px;box-sizing:border-box;border:.8px solid var(--line);background:#fff}
.fac svg{position:absolute;left:11px;top:11px;width:24px;height:24px}
.fac h3{position:absolute;left:11px;top:41px;font-family:'Gelasio',serif;font-weight:400;font-size:8.5px;color:#333}
.fac p{position:absolute;left:11px;top:56px;width:112px;font-size:4.9px;line-height:9.2px;color:#8c8c8c}
.c1{left:95px}.c2{left:242px}.c3{left:388px}
.row1{top:69px}.row2{top:173px}

/* video */
.video{top:1351px;height:202px}
.video-photo{position:absolute;inset:0;background:radial-gradient(ellipse at 50% 85%,rgba(120,95,65,.45),transparent 60%),linear-gradient(180deg,#3a3129,#2a231d 50%,#1b1714)}
.video .eyebrow{top:64px;color:#ddd}
.video .h2{top:75px;color:#fff}
.play{position:absolute;left:299px;top:104px;width:22px;height:22px;border-radius:50%;background:#fff;display:flex;align-items:center;justify-content:center}
.play svg{width:8px;height:8px}

/* gallery */
.gallery{top:1553px;height:314px;background:#fff}
.gallery .eyebrow{top:28px}.gallery .h2{top:40px}
.shot{position:absolute;overflow:hidden;margin:0}
.shot-photo{position:absolute;inset:0}
.shot-cap{position:absolute;left:0;right:0;bottom:0;height:13px;background:rgba(25,22,18,.6);color:var(--gold);font-size:4.3px;letter-spacing:.8px;text-transform:uppercase;display:flex;align-items:center;justify-content:center;font-weight:500}
.g1{left:95px;top:69px;width:135px;height:83px}
.g2{left:242px;top:69px;width:135px;height:83px}
.g3{left:388px;top:69px;width:136px;height:83px}
.g4{left:95px;top:164px;width:208px;height:130px}
.g5{left:315px;top:164px;width:209px;height:130px}
.ph-hotel{background:linear-gradient(180deg,#6f8fb8,#5a7a5a 55%,#3f5d3a)}
.ph-room{background:linear-gradient(160deg,#6b5f55,#3d342d 55%,#1f1a16)}
.ph-event{background:linear-gradient(180deg,#20283a,#3a4663 40%,#2a2a30)}
.ph-spa{background:linear-gradient(170deg,#5c5853,#2f2c29 55%,#151413)}
.ph-rest{background:linear-gradient(160deg,#7a6552,#4a3a2d 55%,#241c16)}

/* testimonial */
.quotes{top:1867px;height:232px;background:#fff}
.quote-card{position:absolute;left:110px;top:28px;width:386px;height:160px;border-radius:8px;overflow:hidden}
.quote-photo{position:absolute;inset:0;background:linear-gradient(100deg,#2e2e2e,#3b3b3b 50%,#262626)}
.quote-card .eyebrow{left:0;width:386px;text-align:center;top:24px;color:#ccc}
.quote-card .h2{left:0;width:386px;text-align:center;top:33px;color:#fff;font-size:15px}
.quote-who{position:absolute;left:0;width:386px;top:70px;text-align:center;font-size:6px;color:#ddd}
.quote-who b{color:var(--gold);font-weight:400}
.quote-text{position:absolute;left:82px;width:222px;top:83px;text-align:center;font-size:5px;line-height:8.4px;color:#ddd}
.arrow{position:absolute;top:67px;width:14px;height:14px;border-radius:50%;background:rgba(255,255,255,.25);display:flex;align-items:center;justify-content:center}
.arrow svg{width:6px;height:6px}
.a-left{left:34px}.a-right{left:337px}
.quote-card .dots{left:176px;top:136px}

/* map */
.map{top:2099px;height:179px}
.map-area{position:absolute;inset:0;background:radial-gradient(ellipse at 20% 30%,#f1f1f1,transparent 45%),radial-gradient(ellipse at 80% 60%,#d2d2d2,transparent 50%),linear-gradient(135deg,#e6e6e6,#dadada 50%,#e2e2e2)}
.pin{position:absolute;left:296px;top:77px;width:28px;height:115px}
.location{top:2278px;height:101px;background:#c8c8c8}
.location p{position:absolute;left:0;width:619px;top:22px;text-align:center;font-size:4.8px;letter-spacing:.4px;color:#333;font-weight:600}
.badge{position:absolute;top:44px;width:33px;height:34px}
.b1{left:217px;background:#1e3b6e;border-radius:2px}
.b2{left:255px;background:#f28a1c;border-radius:2px}
.b3{left:293px;background:#fff;border:.8px solid #7ab6dc;box-sizing:border-box;border-radius:2px}
.b4{left:329px;background:#6a8aa6;border-radius:50%;border:1.5px solid #fff;box-sizing:border-box}
.b5{left:367px;background:#a01c2c;border-radius:50%}

/* newsletter */
.newsletter{top:2379px;height:128px;background:var(--dark)}
.newsletter .eyebrow{top:30px;color:#bbb}
.newsletter .h2{top:41px;color:#fff;font-size:15px}
.signup{position:absolute;left:185px;top:70px;width:248px;height:25px;background:#fff;box-sizing:border-box;border:.8px solid #ddd}
.signup span{position:absolute;left:9px;top:9px;font-size:5px;color:#666}
.signup b{position:absolute;right:3px;top:3px;width:57px;height:17px;background:var(--gold);color:#fff;font-size:4.6px;letter-spacing:.8px;font-weight:600;display:flex;align-items:center;justify-content:center}

/* footer */
.footer{top:2507px;height:188px;background:var(--footer)}
.footer .brand{left:270px;top:33px}
.footer .brand-name{font-size:12px}
.fcol{position:absolute;top:72px;font-size:5px;line-height:9px;color:#555;letter-spacing:.3px}
.fcol h4{margin:0 0 3px;font-size:4.8px;letter-spacing:1px;color:var(--gold);font-weight:600;text-transform:uppercase}
.fc1{left:94px}.fc2{left:215px}.fc3{left:340px}.fc4{left:464px}
.fline{position:absolute;left:0;width:619px;top:163px;height:.6px;background:#ddd}
.copy{position:absolute;left:94px;top:175px;font-size:4.6px;color:#777}
.social{position:absolute;left:477px;top:172px;display:flex;gap:7px}
.social i{width:10px;height:10px;border-radius:50%;background:#9a9a9a}
</style>
</head>
<body>

<!-- full page -->
<div class="panel panel-full">
<div class="page">
  <header class="band nav"><div class="brand"><span class="brand-mark"></span><span class="brand-name">Corvena Hotel</span></div><nav class="menu"><span class="on">Hotel</span><span>Hotel</span><span>Event center</span><span>Contact</span><span>Restaurant Aster</span><span>Gallery</span><i class="menu-div"></i><span>English</span><span class="flag"></span></nav></header>
  <div class="band hero-photo" role="img" aria-label="Hotel restaurant dining room with set tables and tall windows"></div>
  <h1 class="abs hero-title">The true pearl of Rhodes</h1>
  <p class="abs hero-sub">RHODES CITY CENTRE | OPEN ALL YEAR</p>
  <div class="abs hero-btn">ROOMS &amp; SUITES</div>
  <div class="abs booking">
    <div class="field f1">Check in<svg viewBox="0 0 10 10"><rect x="1" y="2" width="8" height="7" fill="none" stroke="#888"/></svg></div>
    <div class="field f2">Check out<svg viewBox="0 0 10 10"><rect x="1" y="2" width="8" height="7" fill="none" stroke="#888"/></svg></div>
    <div class="field f3">1 Adult<svg viewBox="0 0 10 10"><polyline points="2,3 5,6 8,3" fill="none" stroke="#888"/></svg></div>
    <div class="field f4">Children<svg viewBox="0 0 10 10"><polyline points="2,3 5,6 8,3" fill="none" stroke="#888"/></svg></div>
    <div class="field f5">1 Room<svg viewBox="0 0 10 10"><polyline points="2,3 5,6 8,3" fill="none" stroke="#888"/></svg></div>
    <div class="field f6">Promocode</div>
    <div class="field check">CHECK NOW</div>
  </div>
  <p class="abs intro">Hotel Corvena, which blends the calm of the Aegean with architecture that is every inch contemporary, welcomes guests all year round in the very centre of Rhodes Town, a short walk from the port and the Old Town walls. Hotel Corvena is a 4 star superior hotel in Rhodes that has 70 rooms, a spa lounge offering a variety of saunas and other relaxation options, a fitness club, the Aster restaurant and an event centre with cutting-edge sound, lighting and video solutions.</p>

  <section class="band rooms">
    <p class="eyebrow">Corvena Hotel</p><h2 class="h2">Rooms</h2>
    <article class="card r1"><div class="card-photo p-classic" role="img" aria-label="Classic room with bed, lamp and curtained window"></div><div class="card-fade"></div><div class="book"><span>BOOK</span></div><div class="card-info"><p class="price">180€ / Night</p><h3 class="card-name">Classic</h3><p class="desc">Comfortable and elegantly appointed rooms for both business travellers and holiday-makers</p><div class="amenity-row"><div class="amenities"><i></i><i></i><i></i><i></i></div><span class="details">DETAILS →</span></div></div></article>
    <article class="card r2"><div class="card-photo p-exec" role="img" aria-label="Executive room with mirror and entry door"></div><div class="card-fade"></div><div class="book"><span>BOOK</span></div><div class="card-info"><p class="price">210€ / Night</p><h3 class="card-name">Executive</h3><span class="rule"></span></div></article>
    <article class="card r3"><div class="card-photo p-sup" role="img" aria-label="Superior room with bed and armchair"></div><div class="card-fade"></div><div class="book"><span>BOOK</span></div><div class="card-info"><p class="price">265€ / Night</p><h3 class="card-name">Superior</h3></div></article>
  </section>

  <section class="band suite">
    <p class="eyebrow">Corvena Hotel</p><h2 class="h2">Suite</h2>
    <div class="suite-phone"><svg viewBox="0 0 24 24"><path d="M5 3l4 1 1 5-3 2a12 12 0 006 6l2-3 5 1 1 4-3 2C10 21 3 14 3 6z" fill="none" stroke="#b28a56" stroke-width="1.4"/></svg><div><p class="lbl">FOR INFORMATION</p><p class="num">(+30) 22410 64230</p></div></div>
    <article class="card s1"><div class="card-photo p-family" role="img" aria-label="Family room with beds and headboard"></div><div class="card-fade"></div><div class="book"><span>BOOK</span></div><div class="card-info"><p class="price">210€ / Night</p><h3 class="card-name">Family Room</h3><span class="rule"></span></div></article>
    <article class="card s2"><div class="card-photo p-rector" role="img" aria-label="Suite with armchair and double bed"></div><div class="card-fade"></div><div class="book"><span>BOOK</span></div><div class="card-info"><p class="price">265€ / Night</p><h3 class="card-name">Suite Rector</h3><span class="rule"></span></div></article>
    <div class="dots"><i></i><i class="on"></i><i></i></div>
  </section>

  <section class="band facilities">
    <p class="eyebrow">Our Services</p><h2 class="h2">Hotel Facilities</h2>
    <div class="fac c1 row1"><svg viewBox="0 0 24 24" fill="none" stroke="#b28a56" stroke-width="1"><rect x="3" y="7" width="18" height="9" rx="1"/><path d="M5 7l2-4h10l2 4"/><circle cx="7" cy="18" r="2"/><circle cx="17" cy="18" r="2"/></svg><h3>Pick Up &amp; Drop</h3><p>Lorem ipsum dolor sit amet, consectetur adipiscing elit. Nullam sed erat facilisis, fringilla turpis in, dignissim ligula.</p></div>
    <div class="fac c2 row1"><svg viewBox="0 0 24 24" fill="none" stroke="#b28a56" stroke-width="1"><rect x="13" y="3" width="8" height="8"/><path d="M16 9V5h2a1 1 0 010 2h-2"/><rect x="3" y="13" width="12" height="5" rx="1"/><circle cx="6" cy="19" r="1.5"/><circle cx="12" cy="19" r="1.5"/></svg><h3>Parking Space</h3><p>Lorem ipsum dolor sit amet, consectetur adipiscing elit. Nullam sed erat facilisis, fringilla turpis in, dignissim ligula.</p></div>
    <div class="fac c3 row1"><svg viewBox="0 0 24 24" fill="none" stroke="#b28a56" stroke-width="1"><path d="M4 15a8 8 0 0116 0z"/><path d="M2 17h20"/><circle cx="12" cy="6" r="1"/><path d="M5 20h14"/></svg><h3>Room Service</h3><p>Lorem ipsum dolor sit amet, consectetur adipiscing elit. Nullam sed erat facilisis, fringilla turpis in, dignissim ligula.</p></div>
    <div class="fac c1 row2"><svg viewBox="0 0 24 24" fill="none" stroke="#b28a56" stroke-width="1"><path d="M8 16V4h5"/><path d="M15 16V4"/><path d="M8 8h7M8 12h7"/><path d="M2 19c2-1.5 3-1.5 5 0s3 1.5 5 0 3-1.5 5 0 3 1.5 5 0"/></svg><h3>Swimming Pool</h3><p>Lorem ipsum dolor sit amet, consectetur adipiscing elit. Nullam sed erat facilisis, fringilla turpis in, dignissim ligula.</p></div>
    <div class="fac c2 row2"><svg viewBox="0 0 24 24" fill="none" stroke="#b28a56" stroke-width="1"><circle cx="12" cy="10" r="1.5"/><path d="M8.5 6.5a5 5 0 000 7M15.5 6.5a5 5 0 010 7M5.5 3.5a9 9 0 000 13M18.5 3.5a9 9 0 010 13"/><path d="M12 12v9"/></svg><h3>Fibre Internet</h3><p>Lorem ipsum dolor sit amet, consectetur adipiscing elit. Nullam sed erat facilisis, fringilla turpis in, dignissim ligula.</p></div>
    <div class="fac c3 row2"><svg viewBox="0 0 24 24" fill="none" stroke="#b28a56" stroke-width="1"><circle cx="12" cy="12" r="9"/><circle cx="12" cy="12" r="5"/><path d="M4 4l4 4M20 20l-4-4"/></svg><h3>Breakfast</h3><p>Lorem ipsum dolor sit amet, consectetur adipiscing elit. Nullam sed erat facilisis, fringilla turpis in, dignissim ligula.</p></div>
  </section>

  <section class="band video">
    <div class="video-photo" role="img" aria-label="Hotel lounge with armchairs, lamps and wood panelled walls"></div>
    <p class="eyebrow center">Corvena Hotel</p><h2 class="h2 center">from the inside</h2>
    <div class="play"><svg viewBox="0 0 10 10"><polygon points="3,2 8,5 3,8" fill="none" stroke="#333" stroke-width=".8"/></svg></div>
  </section>

  <section class="band gallery">
    <p class="eyebrow">Images</p><h2 class="h2">Image Gallery</h2>
    <figure class="shot g1"><div class="shot-photo ph-hotel" role="img" aria-label="Hotel building seen above the city greenery"></div><figcaption class="shot-cap">Hotel</figcaption></figure>
    <figure class="shot g2"><div class="shot-photo ph-room" role="img" aria-label="Guest room with made bed"></div><figcaption class="shot-cap">Rooms and suites</figcaption></figure>
    <figure class="shot g3"><div class="shot-photo ph-event" role="img" aria-label="Event hall with screen and banquet tables"></div><figcaption class="shot-cap">Event center and Elmar Rood white hall</figcaption></figure>
    <figure class="shot g4"><div class="shot-photo ph-spa" role="img" aria-label="Fitness club with dumbbell racks and machines"></div><figcaption class="shot-cap">Spa-lounge and fitness club</figcaption></figure>
    <figure class="shot g5"><div class="shot-photo ph-rest" role="img" aria-label="Restaurant table set with glasses and plates"></div><figcaption class="shot-cap">Restaurant Aster</figcaption></figure>
  </section>

  <section class="band quotes">
    <div class="quote-card">
      <div class="quote-photo" role="img" aria-label="Dimmed photo of a guest at a desk"></div>
      <p class="eyebrow">Testimonial</p><h2 class="h2">What Our Clients Says</h2>
      <p class="quote-who"><b>Daniel Reyes</b>, Northfield Works</p>
      <p class="quote-text">“They are willing to work with you to get the job done. Nunc et tortor vel elit condimentum tincidunt quis nec quam. Proin elementum nisi sed feugiat molestie. Nulla in ipsum sit amet tortor imperdiet lobortis id mattis arcu. In hac habitasse platea dictumst.”</p>
      <div class="arrow a-left"><svg viewBox="0 0 10 10"><polyline points="6,2 3,5 6,8" fill="none" stroke="#fff"/></svg></div>
      <div class="arrow a-right"><svg viewBox="0 0 10 10"><polyline points="4,2 7,5 4,8" fill="none" stroke="#fff"/></svg></div>
      <div class="dots"><i></i><i class="on wide"></i><i></i><i></i></div>
    </div>
  </section>

  <section class="band map">
    <div class="map-area" role="img" aria-label="Street map of Rhodes Town centre showing the hotel, the port and the main driving routes"></div>
    <svg class="pin" viewBox="0 0 28 115"><line x1="14" y1="36" x2="14" y2="115" stroke="#b28a56" stroke-width="1"/><path d="M14 1a12 12 0 0112 12c0 9-12 22-12 22S2 22 2 13A12 12 0 0114 1z" fill="#b28a56"/><circle cx="14" cy="13" r="7" fill="#fff"/></svg>
  </section>
  <section class="band location">
    <p>Corvena Hotel is situated in the centre of Rhodes Town, a five minute drive from the port and 25 minutes from the airport, at Kastani Street 14.</p>
    <i class="badge b1"></i><i class="badge b2"></i><i class="badge b3"></i><i class="badge b4"></i><i class="badge b5"></i>
  </section>

  <section class="band newsletter">
    <p class="eyebrow center">Subscribe our</p><h2 class="h2 center">Newsletter</h2>
    <div class="signup"><span>Enter your email address</span><b>SEND NOW</b></div>
  </section>

  <footer class="band footer">
    <div class="brand"><span class="brand-mark"></span><span class="brand-name">Corvena Hotel</span></div>
    <div class="fcol fc1"><h4>Hotel Corvena</h4>Kastani 14.<br>85100 Rhodes, Greece<br>P: (+30) 22410 64210<br>E: reception@corvenahotel.gr</div>
    <div class="fcol fc2"><h4>Restaurant Aster</h4>Mon-Fri: 18:00-23:00<br>Sat: 17:00-23:00<br>P: (+30) 22410 64215<br><br>E: info@asterrestaurant.gr<br>W: www.asterrestaurant.gr</div>
    <div class="fcol fc3"><h4>Event centre</h4>P: (+30) 22410 64220<br>E: event@corvenahotel.gr</div>
    <div class="fcol fc4"><h4>Sales department</h4>P: (+30) 22410 64230<br>E: sales@corvenahotel.gr</div>
    <div class="fline"></div>
    <p class="copy">Corvena Hotel © Copyright 2022 - All rights reserved</p>
    <div class="social"><i></i><i></i><i></i></div>
  </footer>
</div>
</div>

<!-- upper page -->
<div class="panel panel-top">
<div class="page">
  <header class="band nav"><div class="brand"><span class="brand-mark"></span><span class="brand-name">Corvena Hotel</span></div><nav class="menu"><span class="on">Hotel</span><span>Hotel</span><span>Event center</span><span>Contact</span><span>Restaurant Aster</span><span>Gallery</span><i class="menu-div"></i><span>English</span><span class="flag"></span></nav></header>
  <div class="band hero-photo" role="img" aria-label="Hotel restaurant dining room with set tables and tall windows"></div>
  <h1 class="abs hero-title">The true pearl of Rhodes</h1>
  <p class="abs hero-sub">RHODES CITY CENTRE | OPEN ALL YEAR</p>
  <div class="abs hero-btn">ROOMS &amp; SUITES</div>
  <div class="abs booking">
    <div class="field f1">Check in<svg viewBox="0 0 10 10"><rect x="1" y="2" width="8" height="7" fill="none" stroke="#888"/></svg></div>
    <div class="field f2">Check out<svg viewBox="0 0 10 10"><rect x="1" y="2" width="8" height="7" fill="none" stroke="#888"/></svg></div>
    <div class="field f3">1 Adult<svg viewBox="0 0 10 10"><polyline points="2,3 5,6 8,3" fill="none" stroke="#888"/></svg></div>
    <div class="field f4">Children<svg viewBox="0 0 10 10"><polyline points="2,3 5,6 8,3" fill="none" stroke="#888"/></svg></div>
    <div class="field f5">1 Room<svg viewBox="0 0 10 10"><polyline points="2,3 5,6 8,3" fill="none" stroke="#888"/></svg></div>
    <div class="field f6">Promocode</div>
    <div class="field check">CHECK NOW</div>
  </div>
  <p class="abs intro">Hotel Corvena, which blends the calm of the Aegean with architecture that is every inch contemporary, welcomes guests all year round in the very centre of Rhodes Town, a short walk from the port and the Old Town walls. Hotel Corvena is a 4 star superior hotel in Rhodes that has 70 rooms, a spa lounge offering a variety of saunas and other relaxation options, a fitness club, the Aster restaurant and an event centre with cutting-edge sound, lighting and video solutions.</p>

  <section class="band rooms">
    <p class="eyebrow">Corvena Hotel</p><h2 class="h2">Rooms</h2>
    <article class="card r1"><div class="card-photo p-classic" role="img" aria-label="Classic room with bed, lamp and curtained window"></div><div class="card-fade"></div><div class="book"><span>BOOK</span></div><div class="card-info"><p class="price">180€ / Night</p><h3 class="card-name">Classic</h3><p class="desc">Comfortable and elegantly appointed rooms for both business travellers and holiday-makers</p><div class="amenity-row"><div class="amenities"><i></i><i></i><i></i><i></i></div><span class="details">DETAILS →</span></div></div></article>
    <article class="card r2"><div class="card-photo p-exec" role="img" aria-label="Executive room with mirror and entry door"></div><div class="card-fade"></div><div class="book"><span>BOOK</span></div><div class="card-info"><p class="price">210€ / Night</p><h3 class="card-name">Executive</h3><span class="rule"></span></div></article>
    <article class="card r3"><div class="card-photo p-sup" role="img" aria-label="Superior room with bed and armchair"></div><div class="card-fade"></div><div class="book"><span>BOOK</span></div><div class="card-info"><p class="price">265€ / Night</p><h3 class="card-name">Superior</h3></div></article>
  </section>

  <section class="band suite">
    <p class="eyebrow">Corvena Hotel</p><h2 class="h2">Suite</h2>
    <div class="suite-phone"><svg viewBox="0 0 24 24"><path d="M5 3l4 1 1 5-3 2a12 12 0 006 6l2-3 5 1 1 4-3 2C10 21 3 14 3 6z" fill="none" stroke="#b28a56" stroke-width="1.4"/></svg><div><p class="lbl">FOR INFORMATION</p><p class="num">(+30) 22410 64230</p></div></div>
    <article class="card s1"><div class="card-photo p-family" role="img" aria-label="Family room with beds and headboard"></div><div class="card-fade"></div><div class="book"><span>BOOK</span></div><div class="card-info"><p class="price">210€ / Night</p><h3 class="card-name">Family Room</h3><span class="rule"></span></div></article>
    <article class="card s2"><div class="card-photo p-rector" role="img" aria-label="Suite with armchair and double bed"></div><div class="card-fade"></div><div class="book"><span>BOOK</span></div><div class="card-info"><p class="price">265€ / Night</p><h3 class="card-name">Suite Rector</h3><span class="rule"></span></div></article>
    <div class="dots"><i></i><i class="on"></i><i></i></div>
  </section>

  <section class="band facilities">
    <p class="eyebrow">Our Services</p><h2 class="h2">Hotel Facilities</h2>
    <div class="fac c1 row1"><svg viewBox="0 0 24 24" fill="none" stroke="#b28a56" stroke-width="1"><rect x="3" y="7" width="18" height="9" rx="1"/><path d="M5 7l2-4h10l2 4"/><circle cx="7" cy="18" r="2"/><circle cx="17" cy="18" r="2"/></svg><h3>Pick Up &amp; Drop</h3><p>Lorem ipsum dolor sit amet, consectetur adipiscing elit. Nullam sed erat facilisis, fringilla turpis in, dignissim ligula.</p></div>
    <div class="fac c2 row1"><svg viewBox="0 0 24 24" fill="none" stroke="#b28a56" stroke-width="1"><rect x="13" y="3" width="8" height="8"/><path d="M16 9V5h2a1 1 0 010 2h-2"/><rect x="3" y="13" width="12" height="5" rx="1"/><circle cx="6" cy="19" r="1.5"/><circle cx="12" cy="19" r="1.5"/></svg><h3>Parking Space</h3><p>Lorem ipsum dolor sit amet, consectetur adipiscing elit. Nullam sed erat facilisis, fringilla turpis in, dignissim ligula.</p></div>
    <div class="fac c3 row1"><svg viewBox="0 0 24 24" fill="none" stroke="#b28a56" stroke-width="1"><path d="M4 15a8 8 0 0116 0z"/><path d="M2 17h20"/><circle cx="12" cy="6" r="1"/><path d="M5 20h14"/></svg><h3>Room Service</h3><p>Lorem ipsum dolor sit amet, consectetur adipiscing elit. Nullam sed erat facilisis, fringilla turpis in, dignissim ligula.</p></div>
    <div class="fac c1 row2"><svg viewBox="0 0 24 24" fill="none" stroke="#b28a56" stroke-width="1"><path d="M8 16V4h5"/><path d="M15 16V4"/><path d="M8 8h7M8 12h7"/><path d="M2 19c2-1.5 3-1.5 5 0s3 1.5 5 0 3-1.5 5 0 3 1.5 5 0"/></svg><h3>Swimming Pool</h3><p>Lorem ipsum dolor sit amet, consectetur adipiscing elit. Nullam sed erat facilisis, fringilla turpis in, dignissim ligula.</p></div>
    <div class="fac c2 row2"><svg viewBox="0 0 24 24" fill="none" stroke="#b28a56" stroke-width="1"><circle cx="12" cy="10" r="1.5"/><path d="M8.5 6.5a5 5 0 000 7M15.5 6.5a5 5 0 010 7M5.5 3.5a9 9 0 000 13M18.5 3.5a9 9 0 010 13"/><path d="M12 12v9"/></svg><h3>Fibre Internet</h3><p>Lorem ipsum dolor sit amet, consectetur adipiscing elit. Nullam sed erat facilisis, fringilla turpis in, dignissim ligula.</p></div>
    <div class="fac c3 row2"><svg viewBox="0 0 24 24" fill="none" stroke="#b28a56" stroke-width="1"><circle cx="12" cy="12" r="9"/><circle cx="12" cy="12" r="5"/><path d="M4 4l4 4M20 20l-4-4"/></svg><h3>Breakfast</h3><p>Lorem ipsum dolor sit amet, consectetur adipiscing elit. Nullam sed erat facilisis, fringilla turpis in, dignissim ligula.</p></div>
  </section>

  <section class="band video">
    <div class="video-photo" role="img" aria-label="Hotel lounge with armchairs, lamps and wood panelled walls"></div>
    <p class="eyebrow center">Corvena Hotel</p><h2 class="h2 center">from the inside</h2>
    <div class="play"><svg viewBox="0 0 10 10"><polygon points="3,2 8,5 3,8" fill="none" stroke="#333" stroke-width=".8"/></svg></div>
  </section>

  <section class="band gallery">
    <p class="eyebrow">Images</p><h2 class="h2">Image Gallery</h2>
    <figure class="shot g1"><div class="shot-photo ph-hotel" role="img" aria-label="Hotel building seen above the city greenery"></div><figcaption class="shot-cap">Hotel</figcaption></figure>
    <figure class="shot g2"><div class="shot-photo ph-room" role="img" aria-label="Guest room with made bed"></div><figcaption class="shot-cap">Rooms and suites</figcaption></figure>
    <figure class="shot g3"><div class="shot-photo ph-event" role="img" aria-label="Event hall with screen and banquet tables"></div><figcaption class="shot-cap">Event center and Elmar Rood white hall</figcaption></figure>
    <figure class="shot g4"><div class="shot-photo ph-spa" role="img" aria-label="Fitness club with dumbbell racks and machines"></div><figcaption class="shot-cap">Spa-lounge and fitness club</figcaption></figure>
    <figure class="shot g5"><div class="shot-photo ph-rest" role="img" aria-label="Restaurant table set with glasses and plates"></div><figcaption class="shot-cap">Restaurant Aster</figcaption></figure>
  </section>
</div>
</div>

<!-- lower page -->
<div class="panel panel-bottom">
<div class="page">
  <section class="band quotes">
    <div class="quote-card">
      <div class="quote-photo" role="img" aria-label="Dimmed photo of a guest at a desk"></div>
      <p class="eyebrow">Testimonial</p><h2 class="h2">What Our Clients Says</h2>
      <p class="quote-who"><b>Daniel Reyes</b>, Northfield Works</p>
      <p class="quote-text">“They are willing to work with you to get the job done. Nunc et tortor vel elit condimentum tincidunt quis nec quam. Proin elementum nisi sed feugiat molestie. Nulla in ipsum sit amet tortor imperdiet lobortis id mattis arcu. In hac habitasse platea dictumst.”</p>
      <div class="arrow a-left"><svg viewBox="0 0 10 10"><polyline points="6,2 3,5 6,8" fill="none" stroke="#fff"/></svg></div>
      <div class="arrow a-right"><svg viewBox="0 0 10 10"><polyline points="4,2 7,5 4,8" fill="none" stroke="#fff"/></svg></div>
      <div class="dots"><i></i><i class="on wide"></i><i></i><i></i></div>
    </div>
  </section>

  <section class="band map">
    <div class="map-area" role="img" aria-label="Street map of Rhodes Town centre showing the hotel, the port and the main driving routes"></div>
    <svg class="pin" viewBox="0 0 28 115"><line x1="14" y1="36" x2="14" y2="115" stroke="#b28a56" stroke-width="1"/><path d="M14 1a12 12 0 0112 12c0 9-12 22-12 22S2 22 2 13A12 12 0 0114 1z" fill="#b28a56"/><circle cx="14" cy="13" r="7" fill="#fff"/></svg>
  </section>
  <section class="band location">
    <p>Corvena Hotel is situated in the centre of Rhodes Town, a five minute drive from the port and 25 minutes from the airport, at Kastani Street 14.</p>
    <i class="badge b1"></i><i class="badge b2"></i><i class="badge b3"></i><i class="badge b4"></i><i class="badge b5"></i>
  </section>

  <section class="band newsletter">
    <p class="eyebrow center">Subscribe our</p><h2 class="h2 center">Newsletter</h2>
    <div class="signup"><span>Enter your email address</span><b>SEND NOW</b></div>
  </section>

  <footer class="band footer">
    <div class="brand"><span class="brand-mark"></span><span class="brand-name">Corvena Hotel</span></div>
    <div class="fcol fc1"><h4>Hotel Corvena</h4>Kastani 14.<br>85100 Rhodes, Greece<br>P: (+30) 22410 64210<br>E: reception@corvenahotel.gr</div>
    <div class="fcol fc2"><h4>Restaurant Aster</h4>Mon-Fri: 18:00-23:00<br>Sat: 17:00-23:00<br>P: (+30) 22410 64215<br><br>E: info@asterrestaurant.gr<br>W: www.asterrestaurant.gr</div>
    <div class="fcol fc3"><h4>Event centre</h4>P: (+30) 22410 64220<br>E: event@corvenahotel.gr</div>
    <div class="fcol fc4"><h4>Sales department</h4>P: (+30) 22410 64230<br>E: sales@corvenahotel.gr</div>
    <div class="fline"></div>
    <p class="copy">Corvena Hotel © Copyright 2022 - All rights reserved</p>
    <div class="social"><i></i><i></i><i></i></div>
  </footer>
</div>
</div>

</body>
</html>
```